Revamp Of Landing Page For an Automated AI Voice Agents Agency

here is my current landing page https://app.brightfernpromotionhub.biz/v2/preview/WXKRPmQ4hLzYBvNdTeGS?notrack=true

Please use all my current content and imagery of ai agents in your new design. Make it easy to ready, easy to navigate and easy to understand

I am looking for a SLEEK shiny polished looking website. I like Dark themed sites but am open to see light themed sites too so please dont be shy.

The site should have an Ai Voice Agent Theme about it. Maybe look and feel of futureistic but simple and not intimidating to the average person...

Here are a couple website designs I like for reference:
https://q7v.io/
https://ai-bots.marekholvin.com/
https://chatwelmo.com/ai-agents

Target Market(s)

b2b

Industry/Entity Type

AI Voice Agents

Coding

Coded - Design and coding required

Font styles to use
Other font styles liked:
• open

Requirements
Must have
• all elements and content and images used in existing design.
Nice to have
• open
Should not have
• open

```html
<!DOCTYPE html>
<html lang="en">
<head>
<meta charset="utf-8">
<title>Voxora Ai — AI Voice Agents</title>
<link href="https://fonts.googleapis.com/css2?family=Lexend:wght@500;600;700&family=Montserrat:wght@400;500;600;700&display=swap" rel="stylesheet">
<style>
:root{
  --bg:#0d0418;
  --bg-deep:#08020f;
  --card:#120722;
  --card-line:#3a1f5c;
  --white:#ffffff;
  --muted:#cfc6dc;
  --purple:#7b2cf0;
  --magenta:#d61fd0;
  --pink:#ff2f86;
  --orange:#ff6a2a;
  --lilac:#c8a8ff;
  --blue:#2a3ad8;
}
*{margin:0;padding:0;box-sizing:border-box}
html,body{width:1200px;height:4669px;overflow:hidden}
body{position:relative;background:radial-gradient(ellipse 700px 500px at 900px 300px,#3a0f6b 0%,transparent 70%),radial-gradient(ellipse 800px 600px at 200px 2450px,#2a0d52 0%,transparent 70%),var(--bg);color:var(--white);font-family:"Montserrat",sans-serif}
.abs{position:absolute}
h1,h2,h3,.brand{font-family:"Lexend",sans-serif}
.brand{font-weight:600;color:var(--white);letter-spacing:3px;display:flex;align-items:center;gap:10px}
.brand .dot{width:14px;height:14px;border-radius:50%;background:var(--white)}
.btn{position:absolute;display:flex;align-items:center;justify-content:center;height:33px;width:202px;background:linear-gradient(90deg,var(--purple),var(--magenta));color:var(--white);font-size:13px;font-weight:500;border-radius:2px}
.note{position:absolute;font-size:12.5px;line-height:19px;color:var(--muted)}
.note .link{color:var(--pink);text-decoration:underline}
.shape{position:absolute}
/* hero */
.hero-title{left:141px;top:160px;font-size:45px;line-height:48px;font-weight:700;text-transform:uppercase;background:linear-gradient(90deg,var(--pink),var(--orange) 60%,var(--magenta));-webkit-background-clip:text;background-clip:text;color:transparent;letter-spacing:-1px}
.hero-sub{left:141px;top:262px;font-size:15.5px;line-height:23px;font-weight:700}
.hero-visual{left:525px;top:55px;width:675px;height:490px;background:radial-gradient(ellipse at 60% 45%,#6b4aa8 0%,#3a1f6e 35%,#1a0a33 70%,transparent 100%)}
/* workforce */
.section-title{font-size:31px;line-height:38px;font-weight:600;text-transform:uppercase}
.agent-card{position:absolute;width:290px;height:437px;background:linear-gradient(180deg,#1a0b30,#0f0620 70%);border:1px solid var(--card-line);text-align:center}
.agent-card.glow-pink{background:linear-gradient(180deg,#5a0f7a 0%,#2a0a45 45%,#120722 100%)}
.agent-card.glow-green{background:linear-gradient(180deg,#0f2a1c,#0a0f14 60%)}
.agent-card.glow-blue{background:linear-gradient(180deg,#101a4a,#0b0a22 60%)}
.agent-card.glow-orange{background:linear-gradient(180deg,#3a1a10,#1a0b0a 60%)}
.agent-photo{position:absolute;left:8px;top:8px;width:272px;height:176px}
.agent-icon{position:absolute;left:120px;top:158px;width:52px;height:52px;border-radius:50%;border:2px solid rgba(255,255,255,.6)}
.agent-card h3{position:absolute;top:232px;left:0;right:0;font-size:16px;font-weight:500}
.agent-card .lead{position:absolute;top:264px;left:22px;right:22px;font-size:11px;line-height:17px;font-weight:700}
.agent-card p{font-size:11px;line-height:17px;color:var(--muted)}
.agent-card .body{position:absolute;left:22px;right:22px}
/* band */
.band{left:0;top:1686px;width:1200px;height:417px;background:radial-gradient(ellipse 600px 180px at 600px 360px,#3a55ff 0%,#1a2a9a 35%,transparent 75%),linear-gradient(180deg,var(--bg) 0%,#0a1048 55%,#0a0a30 100%)}
.center{left:0;width:1200px;text-align:center}
.eyebrow{font-size:14.5px;font-weight:600;color:var(--orange);letter-spacing:.5px}
/* features */
.feature{position:absolute;width:254px;text-align:center}
.feature-icon{width:82px;height:82px;border-radius:50%;margin:0 auto}
.feature h3{margin-top:36px;font-family:"Montserrat",sans-serif;font-size:14.5px;font-weight:600;letter-spacing:.5px}
.feature p{margin-top:14px;font-size:11.5px;line-height:17px;color:var(--muted)}
/* lightning */
.bolt{left:598px;top:2493px;width:472px;height:444px;background:radial-gradient(ellipse 150px 220px at 55% 50%,#ff6a2a 0%,#b0304a 40%,#3a0f5a 75%,transparent 100%)}
/* promise */
.promise-card{position:absolute;background:linear-gradient(180deg,#2a0f4a,#150828);border:1px solid var(--card-line);text-align:center}
.promise-card.green{background:linear-gradient(180deg,#0e3a22,#0a1410)}
.promise-card.blue{background:linear-gradient(180deg,#0f1d5a,#0a0c22)}
.promise-icon{width:80px;height:80px;border-radius:50%;margin:34px auto 0}
.promise-card h3{margin-top:28px;font-family:"Montserrat",sans-serif;font-size:15px;line-height:19px;font-weight:600}
.promise-card p{margin-top:12px;font-size:11.5px;line-height:17px;color:var(--muted)}
.stars{display:flex;justify-content:center;gap:8px;margin-top:14px}
/* faq */
.faq-line{left:285px;top:3647px;width:1px;height:270px;background:#5a3b86}
.faq-q{position:absolute;left:263px;width:674px;height:40px;background:#2a2238;display:flex;align-items:center;padding-left:50px;font-size:14.5px;font-weight:600}
.faq-q::before{content:"";position:absolute;left:11px;top:9px;width:22px;height:22px;border-radius:50%;border:2px solid var(--lilac);background:#3b1e66}
.faq-a{position:absolute;left:313px;width:600px;font-size:11.5px;line-height:21px;color:var(--muted)}
/* footer */
.footer-row{left:141px;width:918px;top:4481px;display:flex;justify-content:space-between;font-size:11px;color:var(--muted)}
.refund-bar{left:141px;top:4521px;width:918px;height:33px;background:linear-gradient(90deg,var(--magenta),var(--pink));display:flex;align-items:center;justify-content:center;font-size:11px}
.small{font-size:11px;line-height:18px;color:var(--muted)}
</style>
</head>
<body>

<!-- decorative outline triangles -->
<svg class="shape" style="left:650px;top:30px" width="90" height="100" aria-hidden="true"><polygon points="5,5 85,50 5,95" fill="none" stroke="#5b1fa0" stroke-width="2" opacity=".6"/></svg>
<svg class="shape" style="left:0;top:640px" width="80" height="160" aria-hidden="true"><polyline points="0,10 70,80 0,150" fill="none" stroke="#ff2f86" stroke-width="2" opacity=".5"/></svg>
<svg class="shape" style="left:1090px;top:2700px" width="110" height="160" aria-hidden="true"><polyline points="110,10 10,80 110,150" fill="none" stroke="#ff2f86" stroke-width="2" opacity=".5"/></svg>

<!-- header -->
<div class="brand abs" style="left:141px;top:22px;font-size:27px"><span>VOXORA</span><span class="dot"></span></div>

<!-- hero -->
<div class="hero-visual abs" role="img" aria-label="AI robot agent wearing a headset working at a laptop"></div>
<h1 class="hero-title abs">AI Voice Agents<br>That Answer Calls,</h1>
<div class="hero-sub abs">Book Appts, Send Emails, Text Messages,<br>Follow Up Reminders, Transfer Calls &amp; More<br>For You 24 Hours 7 Days A Week!</div>
<div class="btn" style="left:141px;top:359px">Get An Instant Free Demo</div>
<p class="note" style="left:141px;top:413px;width:370px">We Will Create An Ai Agent Customized For Your Business At No Cost. Simply <span class="link">Click The Button</span> Above And Your Very Own Ai Agent Will Be Calling You In Just A Couple Minutes. Experience The Magic And Get Ready To Be Very Impressed!</p>

<!-- workforce -->
<h2 class="section-title abs" style="left:141px;top:673px">Meet Your<br>New AI-<br>Powered<br>Workforce</h2>
<div class="btn" style="left:141px;top:852px">Get An Instant Free Demo</div>
<p class="note" style="left:141px;top:908px;width:300px">We Will Create An Ai Agent Customized For Your Business At No Cost. Simply <span class="link">Click The Button</span> Above And Your Very Own Ai Agent Will Be Calling You In Just A Couple Minutes. Experience The Magic And Get Ready To Be Very Impressed!</p>

<div class="agent-card" style="left:453px;top:671px">
  <div class="agent-photo" role="img" aria-label="Sales agent with headset in a city office" style="background:linear-gradient(180deg,#8a93a6,#3c4258)"></div>
  <div class="agent-icon" role="img" aria-label="Sales agent icon" style="background:radial-gradient(#8a4cff,#4a1aa8)"></div>
  <h3>Ai Sales Agent</h3>
  <div class="body" style="top:266px"><p>Brian will take your inbound sales calls. Will give all detailed information to the customer, answer questions in a normal conversational tone and can book sales appointments or transfer hot prospects to a human to close the sale.</p></div>
</div>

<div class="agent-card glow-pink" style="left:769px;top:671px">
  <div class="agent-photo" role="img" aria-label="Receptionist agent with headset in a cyan lit room" style="background:linear-gradient(180deg,#2aa8b8,#1a4a6a)"></div>
  <div class="agent-icon" role="img" aria-label="Receptionist icon" style="background:radial-gradient(#ff5ab0,#c01a8a)"></div>
  <h3>Ai Receptionist</h3>
  <div class="lead" style="top:264px">Takes Overflow and After Hours Calls or Can Take Calls 24/7 &amp; Transfer To Appropriate Dept.</div>
  <div class="body" style="top:321px"><p>Cody handles all your calls 24/7. You can also set him to only take overflow calls and after hours. He can send emails and sms messages and even book appointments over the call</p></div>
</div>

<div class="agent-card glow-green" style="left:141px;top:1135px">
  <div class="agent-photo" role="img" aria-label="Robot appointment setter with headset" style="background:linear-gradient(180deg,#6a7480,#2a3038)"></div>
  <div class="agent-icon" role="img" aria-label="Calendar icon" style="background:radial-gradient(#3ad86a,#0f7a30)"></div>
  <h3>Ai Appointment Setter</h3>
  <div class="lead">Book Appts &amp; Reservations On Auto Pilot</div>
  <div class="body" style="top:281px"><p>Bobby offers business advice, helps brainstorm ideas, and provides insights on growth tactics to support your entrepreneurial journey.</p></div>
</div>

<div class="agent-card glow-blue" style="left:453px;top:1135px">
  <div class="agent-photo" role="img" aria-label="Agents working at laptops with holographic screens" style="background:linear-gradient(180deg,#1a4a7a,#0a1a3a)"></div>
  <div class="agent-icon" role="img" aria-label="Lead qualifier icon" style="background:radial-gradient(#3a6aff,#1a2aa8)"></div>
  <h3>Ai Lead Qualifier</h3>
  <div class="lead">Conversate With Prospects To Qualify Before Handing Over To Sales Team</div>
  <div class="body" style="top:298px"><p>All of our ai agents gather information and qualify leads. If they are interested in the services on the call then our ai agents will assist them with booking an appointment with our sales team over the call.</p></div>
</div>

<div class="agent-card glow-orange" style="left:769px;top:1135px">
  <div class="agent-photo" role="img" aria-label="Robot follow up assistant in a bright studio" style="background:linear-gradient(180deg,#5a7080,#2a3440)"></div>
  <div class="agent-icon" role="img" aria-label="Reminder icon" style="background:radial-gradient(#ffb03a,#d8701a)"></div>
  <h3>Ai Follow Up Reminders</h3>
  <div class="lead">Calls, Sends SMS &amp; Email Reminders</div>
  <div class="body" style="top:281px"><p>Sam handles all the follow up calls, appt reminders and sends out the email and sms reminders too.</p></div>
</div>

<!-- band -->
<div class="band abs" role="img" aria-label="Glowing blue digital wave landscape"></div>
<div class="center abs eyebrow" style="top:1767px">INSTALL THE POWER OF AI FOR YOUR BUSINESS</div>
<h2 class="center abs" style="top:1798px;font-size:30px;font-weight:600;text-transform:uppercase">Your Wish Is Their Command</h2>
<p class="center abs" style="top:1862px;font-size:14.5px;font-weight:600">Your New Ai Agents Will Never Call In Sick And Will Never Complain!</p>
<p class="abs" style="left:270px;width:660px;top:1894px;text-align:center;font-size:14.5px;line-height:23px;font-weight:600">With your new team of AI Agents, handling inbound calls, sending emails and sms messages, booking appointments and handling customer service inquiries is going to save you a ton of time and money.</p>

<!-- features -->
<h2 class="center abs" style="top:2128px;font-size:30px;font-weight:600;text-transform:uppercase">An Employee That Never Gets Sick!</h2>
<div class="feature" style="left:219px;top:2203px">
  <div class="feature-icon" role="img" aria-label="Glowing brain circuit icon" style="background:radial-gradient(#1f6a4a 0%,#0a2a1e 60%,transparent 72%);border:1px solid #2a7a5a"></div>
  <h3>TRAINED IN SECONDS</h3><p>Learns Your Entire Website<br>In Seconds</p>
</div>
<div class="feature" style="left:473px;top:2203px">
  <div class="feature-icon" role="img" aria-label="Glowing globe icon" style="background:radial-gradient(#6a1f6a 0%,#2a0a2a 60%,transparent 72%);border:1px solid #8a2a8a"></div>
  <h3>WORLDWIDE</h3><p>Works Anywhere In<br>The Globe</p>
</div>
<div class="feature" style="left:727px;top:2203px">
  <div class="feature-icon" role="img" aria-label="Glowing head with gears icon" style="background:radial-gradient(#6a3a1a 0%,#2a140a 60%,transparent 72%);border:1px solid #9a5a2a"></div>
  <h3>USER-FRIENDLY</h3><p>Your Ai Agents Sound As If<br>They're Real Humans</p>
</div>

<!-- ready to be hired -->
<div class="bolt abs" role="img" aria-label="Glowing lightning bolt above the words lightning responses"></div>
<h2 class="section-title abs" style="left:141px;top:2548px;font-size:30px">Our AI Agents<br>Our Ready To Be Hired</h2>
<div class="abs eyebrow" style="left:141px;top:2652px">LIGHTNING-FAST RESPONSES</div>
<p class="abs" style="left:141px;top:2680px;font-size:21px;line-height:28px;font-weight:600">Instant answers, no coffee, bathroom<br>or lunch breaks needed</p>
<div class="btn" style="left:141px;top:2759px">Get An Instant Free Demo</div>
<p class="note" style="left:141px;top:2815px;width:370px">We Will Create An Ai Agent Customized For Your Business At No Cost. Simply <span class="link">Click The Button</span> Above And Your Very Own Ai Agent Will Be Calling You In Just A Couple Minutes. Experience The Magic And Get Ready To Be Very Impressed!</p>

<!-- promise -->
<div class="promise-card" style="left:141px;top:3076px;width:290px;height:348px">
  <h3 style="margin-top:50px;font-family:'Lexend',sans-serif;font-size:24px;line-height:32px;font-weight:500;text-transform:uppercase">After Our<br>Customers Have<br>A Conversation<br>With Their New<br>AI Voice Agent<br>They Give Us 5<br>Stars!</h3>
  <div class="stars">
    <svg width="26" height="26" viewBox="0 0 24 24" aria-hidden="true"><polygon points="12,1 15,9 23,9 16.5,14 19,22 12,17 5,22 7.5,14 1,9 9,9" fill="#ff8a1a"/></svg>
    <svg width="26" height="26" viewBox="0 0 24 24" aria-hidden="true"><polygon points="12,1 15,9 23,9 16.5,14 19,22 12,17 5,22 7.5,14 1,9 9,9" fill="#ff8a1a"/></svg>
    <svg width="26" height="26" viewBox="0 0 24 24" aria-hidden="true"><polygon points="12,1 15,9 23,9 16.5,14 19,22 12,17 5,22 7.5,14 1,9 9,9" fill="#ff8a1a"/></svg>
    <svg width="26" height="26" viewBox="0 0 24 24" aria-hidden="true"><polygon points="12,1 15,9 23,9 16.5,14 19,22 12,17 5,22 7.5,14 1,9 9,9" fill="#ff8a1a"/></svg>
    <svg width="26" height="26" viewBox="0 0 24 24" aria-hidden="true"><polygon points="12,1 15,9 23,9 16.5,14 19,22 12,17 5,22 7.5,14 1,9 9,9" fill="#ff8a1a"/></svg>
  </div>
</div>
<h2 class="abs" style="left:453px;width:606px;top:3082px;text-align:center;font-size:30px;font-weight:600;text-transform:uppercase">Our Promise To You:</h2>
<div class="promise-card green" style="left:453px;top:3169px;width:290px;height:255px">
  <div class="promise-icon" role="img" aria-label="Calendar showing 14 days" style="background:radial-gradient(#2ac85a,#0f6a2a)"></div>
  <h3>14-DAY MONEY-BACK<br>GUARANTEE*</h3>
</div>
<div class="promise-card blue" style="left:769px;top:3169px;width:290px;height:255px">
  <div class="promise-icon" role="img" aria-label="24 hour support clock" style="background:radial-gradient(#3a6aff,#1a2ab8)"></div>
  <h3>24/7 CUSTOMER<br>SUPPORT</h3>
  <p>Often praised for our friendly<br>&amp; helpful support team</p>
</div>

<!-- faq -->
<h2 class="center abs" style="top:3557px;font-size:30px;font-weight:600;text-transform:uppercase">Do You Have Questions?</h2>
<div class="faq-line abs"></div>
<div class="faq-q" style="top:3627px">What exactly are the AI Voice Agents?</div>
<p class="faq-a" style="top:3684px">AI Voice Agents are specialized human sounding bots, having smart and masterful conversations and each is expertly trained in seconds for a specific business function.</p>
<div class="faq-q" style="top:3744px">How will these AI Voice Agents benefit</div>
<p class="faq-a" style="top:3801px">Ai Voice Agents Answer Calls, Book Appts, Send Emails, Text Messages, Follow Up Reminders &amp; More For You 24/7!</p>
<div class="faq-q" style="top:3861px">Are they easy to use?</div>
<p class="faq-a" style="top:3917px">We provide a done for you service. We create your AI Voice Agent and launch it within days!</p>

<!-- final cta -->
<h2 class="center abs" style="top:4068px;font-size:33px;line-height:39px;font-weight:600;text-transform:uppercase">These AI Agents Can Help<br>Your Business Tremendously.<br>Imagine The Possibilities</h2>
<div class="btn" style="left:499px;top:4197px">Get An Instant Free Demo</div>
<p class="note" style="left:330px;width:540px;top:4254px;text-align:center">We Will Create An Ai Agent Customized For Your Business At No Cost. Simply <span class="link">Click The Button</span> Above And Your Very Own Ai Agent Will Be Calling You In Just A Couple Minutes. Experience The Magic And Get Ready To Be Very Impressed!</p>

<!-- footer -->
<div class="brand abs" style="left:0;width:1200px;justify-content:center;top:4392px;font-size:35px"><span>VOXORA</span><span class="dot" style="width:16px;height:16px"></span></div>
<div class="footer-row abs"><span>© 2025 Voxora Ai. All rights reserved.</span><span>Disclaimer: Privacy | Terms &amp; Conditions | Earnings &amp; Products Disclaimer</span></div>
<div class="refund-bar abs">*14-Day Money Back Guarantee Terms: If you use the ai agents and you're not happy. Then you can contact us in the first 14 days for a full refund.</div>
<p class="center abs small" style="top:4573px">Do you have questions about ( ) Please email ( )</p>
<p class="center abs small" style="top:4620px">IMPORTANT: This site is not a part of the Socialnest website or Socialnest Inc. Additionally,<br>this site is NOT endorsed by Socialnest in any way. SOCIALNEST is a trademark of SOCIALNEST, Inc.</p>

</body>
</html>
```